Tarvex Consulting

Hi,
I have my own network consulting business (just me)
and need to get a logo and business card design together,

Based in New Zealand,

Gareth Holloway
Unified Communications and Network Architect

/design engineer,
and would like this to be the basis for personal branding and company identity

• I have the basis for a optional logo - needs color -

```html
<!DOCTYPE html>
<html lang="en">
<head>
<meta charset="utf-8">
<title>Tarvex Consulting – Business Card</title>
<link rel="stylesheet" href="https://fonts.googleapis.com/css2?family=Questrial&family=Jura:wght@700&display=swap">
<style>
  :root {
    --brand-blue: #1ba4dd;
    --brand-blue-light: #7fcbee;
    --brand-blue-pale: #bfe4f6;
    --ink: #2b2b2b;
    --paper: #ffffff;
    --paper-shade: #e4e4e4;
    --stage: #eef1f4;
  }
  * { box-sizing: border-box; margin: 0; padding: 0; }
  html, body { width: 1200px; height: 1200px; overflow: hidden; }
  body {
    background: var(--stage);
    display: flex;
    flex-direction: column;
    align-items: center;
    justify-content: center;
    gap: 60px;
    font-family: "Questrial", "Helvetica Neue", Arial, sans-serif;
  }
  .card {
    position: relative;
    width: 900px;
    height: 514px;
    overflow: hidden;
    box-shadow: 0 10px 30px rgba(0,0,0,0.18);
  }

  /* Front */
  .card-front {
    background: radial-gradient(ellipse 90% 85% at 62% 55%, var(--paper) 45%, var(--paper-shade) 100%);
  }
  .brand {
    position: absolute;
    left: 86px;
    top: 120px;
    display: flex;
    align-items: center;
    gap: 22px;
  }
  .brand-dot {
    width: 74px;
    height: 74px;
    border-radius: 50%;
    background: var(--brand-blue);
  }
  .brand-name {
    font-family: "Jura", "Questrial", sans-serif;
    font-weight: 700;
    font-size: 52px;
    line-height: 0.95;
    letter-spacing: 1px;
    text-transform: uppercase;
    color: var(--brand-blue);
  }
  .contact-stripe {
    position: absolute;
    left: 0; right: 0;
    top: 372px;
    height: 22px;
    background: var(--brand-blue);
  }
  .footer-band {
    position: absolute;
    left: 0; right: 0;
    bottom: 0;
    height: 50px;
    background: var(--brand-blue);
  }
  .person {
    position: absolute;
    left: 48px;
    top: 298px;
  }
  .person-name {
    font-size: 42px;
    color: var(--brand-blue);
    line-height: 1;
    letter-spacing: 0.5px;
  }
  .person-role {
    margin-top: 6px;
    font-size: 13px;
    color: var(--ink);
  }
  .contact {
    position: absolute;
    display: flex;
    align-items: center;
    gap: 8px;
    font-size: 17px;
    color: var(--ink);
    letter-spacing: 0.5px;
  }
  .contact svg { width: 18px; height: 18px; flex: none; }
  .contact-phone { left: 478px; top: 336px; }
  .contact-web { left: 666px; top: 336px; }
  .contact-email { left: 56px; top: 412px; }

  /* Back */
  .card-back {
    display: flex;
    align-items: center;
    justify-content: center;
    background: var(--brand-blue);
  }
  .back-pattern {
    position: absolute;
    inset: 0;
    background: radial-gradient(ellipse 80% 90% at 70% 10%, var(--brand-blue-pale) 0%, var(--brand-blue-light) 40%, var(--brand-blue) 100%);
  }
  .back-brand {
    position: relative;
    display: flex;
    align-items: center;
    gap: 20px;
  }
  .back-brand .brand-dot { background: var(--paper); width: 64px; height: 64px; }
  .back-brand .brand-name { color: var(--paper); font-size: 46px; }
</style>
</head>
<body>

  <section class="card card-front" aria-label="Business card front">
    <div class="brand">
      <span class="brand-dot" aria-hidden="true"></span>
      <span class="brand-name">Tarvex<br>Consulting</span>
    </div>

    <div class="person">
      <p class="person-name">Gareth Holloway</p>
      <p class="person-role">Unified Communications and Network Architect / Design Engineer</p>
    </div>

    <p class="contact contact-phone">
      <svg viewBox="0 0 24 24" aria-hidden="true"><path fill="#2b2b2b" d="M6.6 2.5c.6-.4 1.4-.3 1.8.3l2 3c.4.6.3 1.3-.2 1.8l-1.4 1.2c.8 2.4 2.3 4.6 4.4 6.2l1.5-1.1c.6-.4 1.3-.4 1.8.1l2.6 2.5c.5.5.5 1.3 0 1.8l-1.5 1.6c-1 1-2.6 1.3-3.9.6C8.4 17.9 5.2 13.6 4.3 8.4c-.2-1.4.3-2.8 1.4-3.7z"/></svg>
      001 555 010 284
    </p>
    <p class="contact contact-web">
      <svg viewBox="0 0 24 24" aria-hidden="true" fill="none" stroke="#2b2b2b" stroke-width="1.6"><circle cx="12" cy="12" r="9.5"/><ellipse cx="12" cy="12" rx="4.2" ry="9.5"/><path d="M2.5 12h19M4 7h16M4 17h16"/></svg>
      www.tarvexnet.example
    </p>

    <div class="contact-stripe"></div>

    <p class="contact contact-email">
      <svg viewBox="0 0 24 24" aria-hidden="true" fill="none" stroke="#2b2b2b" stroke-width="1.6"><rect x="2.5" y="5" width="19" height="14"/><path d="M2.5 5l9.5 8 9.5-8M2.5 19l7-6.5M21.5 19l-7-6.5"/></svg>
      gareth@tarvexnet.example
    </p>

    <div class="footer-band"></div>
  </section>

  <section class="card card-back" aria-label="Business card back">
    <div class="back-pattern" role="img" aria-label="Repeating pattern of pale blue brand shapes"></div>
    <div class="back-brand">
      <span class="brand-dot" aria-hidden="true"></span>
      <span class="brand-name">Tarvex<br>Consulting</span>
    </div>
  </section>

</body>
</html>
```